BWP Business Card

A double sided business card based on your "Brindlewood Partners Ltd" Logo. To use the "BWP" logo on 1 side and the full company logo on the reverse.

Detials to be included:

Name: Tomas Wheeler
Postion: Consultant Orthotist & Expert Witness
T: +44 (0) 7700 938271
F: +44 (0) 7654 8820

```html
<!DOCTYPE html>
<html lang="en">
<head>
<meta charset="utf-8">
<title>BWP Business Card</title>
<link href="https://fonts.googleapis.com/css2?family=Tinos:wght@400;700&display=swap" rel="stylesheet">
<style>
  :root {
    --navy: #123d72;
    --grey: #8c8f93;
    --rule: #c6c8cb;
    --text: #55585c;
    --paper: #ffffff;
    --backdrop: #e9e7e3;
  }
  * { box-sizing: border-box; margin: 0; padding: 0; }
  html, body { width: 1200px; height: 720px; overflow: hidden; }
  body {
    background: var(--backdrop);
    font-family: "Tinos", "Times New Roman", serif;
    color: var(--text);
    position: relative;
  }
  .card {
    position: absolute;
    top: 212px;
    width: 520px;
    height: 297px;
    background: var(--paper);
    box-shadow: 0 2px 6px rgba(0,0,0,0.15);
    overflow: hidden;
  }
  .card--details { left: 60px; }
  .card--brand { left: 620px; }

  .brand-name {
    display: flex;
    align-items: center;
    gap: 12px;
    font-family: "Tinos", "Times New Roman", serif;
    font-weight: 700;
    color: var(--navy);
    white-space: nowrap;
  }
  .brand-name__square { background: var(--navy); flex: none; }

  .card--details .brand-name {
    position: absolute; left: 0; right: 0; top: 46px;
    justify-content: center; font-size: 26px;
  }
  .card--details .brand-name__square { width: 22px; height: 22px; }

  .card--brand .brand-name {
    position: absolute; left: 0; right: 0; top: 50%;
    transform: translateY(-50%);
    justify-content: center; font-size: 32px;
  }
  .card--brand .brand-name__square { width: 28px; height: 28px; }

  .stripe { position: absolute; left: 0; right: 0; background: var(--navy); }
  .stripe--thin { top: 118px; height: 3px; }
  .rule--grey { position: absolute; left: 0; right: 0; top: 125px; height: 1px; background: var(--rule); }
  .stripe--band {
    top: 132px; height: 30px;
    display: flex; align-items: center; justify-content: center;
    color: var(--paper); font-size: 13px;
  }
  .band__name { font-weight: 700; font-size: 15px; margin-right: 5px; }

  .details { position: absolute; top: 186px; left: 0; right: 0; display: flex; }
  .details__address {
    width: 230px; text-align: right; padding-right: 18px; padding-top: 22px;
    font-size: 13px; line-height: 1.6; font-style: normal; color: var(--text);
  }
  .details__divider { width: 1px; height: 80px; background: var(--rule); }
  .details__contacts { list-style: none; padding-left: 16px; font-size: 12.5px; line-height: 1.95; color: var(--text); }
  .details__contacts li { display: flex; align-items: center; gap: 7px; }
  .icon { width: 11px; height: 11px; fill: var(--text); }
</style>
</head>
<body>

<section class="card card--details" aria-label="Business card, details side">
  <div class="brand-name">
    <span class="brand-name__square"></span>
    <span>Brindlewood Partners Ltd</span>
  </div>

  <div class="stripe stripe--thin"></div>
  <div class="rule--grey"></div>
  <div class="stripe stripe--band">
    <span class="band__name">Tomas Wheeler,</span>
    <span class="band__role">Consultant Orthotist &amp; Expert Witness</span>
  </div>

  <div class="details">
    <address class="details__address">
      18 Ashcombe Road Kingston<br>Surrey, KT2 4PN
    </address>
    <span class="details__divider"></span>
    <ul class="details__contacts">
      <li>
        <svg class="icon" viewBox="0 0 12 12" aria-hidden="true"><path d="M2.5 0.8l2 2-1 1.4c.6 1.4 1.7 2.6 3.2 3.3l1.3-1 2.2 2-1.2 2.2C5 10.4 1.4 6.9 0.9 2z"/></svg>
        +44 (0) 7700 938271
      </li>
      <li>
        <svg class="icon" viewBox="0 0 12 12" aria-hidden="true"><path d="M1 8V5l1.5-3h7L11 5v3H10v1.5H8.5V8h-5v1.5H2V8zm2-3h6L8.2 3H3.8z"/></svg>
        +44 (0) 7654 8820
      </li>
      <li>
        <svg class="icon" viewBox="0 0 12 12" aria-hidden="true"><path d="M1 3h10v6.5H1zm1 .8L6 6.6 10 3.8z" fill-rule="evenodd"/></svg>
        tomas@brindlewoodpartners.co.uk
      </li>
    </ul>
  </div>
</section>

<section class="card card--brand" aria-label="Business card, name side">
  <div class="brand-name">
    <span class="brand-name__square"></span>
    <span>Brindlewood Partners Ltd</span>
  </div>
</section>

</body>
</html>
```